The Linen Loft Co

We need a business card design for our wardrobe company.
Please visit our website www.gentlelinenlofts.com to get an idea of who we are.

```html
<!DOCTYPE html>
<html lang="en">
<head>
<meta charset="utf-8">
<title>The Linen Loft Co – Business Card</title>
<link href="https://fonts.googleapis.com/css2?family=Jost:wght@400;500&display=swap" rel="stylesheet">
<style>
  :root {
    --page-bg: #2a2a2a;
    --card-top: #bdbdbd;
    --card-mid: #5a5a5a;
    --card-bottom: #0f0f0f;
    --ink-dark: #141414;
    --ink-muted: #d0d0d0;
    --ink-light: #ececec;
    --divider: rgba(255,255,255,0.55);
  }
  * { margin: 0; padding: 0; box-sizing: border-box; }
  html, body {
    width: 1200px;
    height: 800px;
    overflow: hidden;
    background: var(--page-bg);
    font-family: "Jost", sans-serif;
  }
  .business-card {
    position: absolute;
    left: 100px;
    top: 118px;
    width: 1000px;
    height: 563px;
    background: linear-gradient(to bottom, var(--card-top) 0%, var(--card-mid) 50%, var(--card-bottom) 100%);
  }
  .brand-square {
    position: absolute;
    left: 196px;
    top: 232px;
    width: 66px;
    height: 66px;
    background: var(--ink-dark);
  }
  .brand-text {
    position: absolute;
    left: 279px;
    top: 226px;
    width: 280px;
    display: flex;
    flex-direction: column;
    align-items: center;
  }
  .brand-name {
    font-size: 21px;
    font-weight: 500;
    color: var(--ink-dark);
    letter-spacing: 0.4px;
    text-transform: uppercase;
    line-height: 1.2;
  }
  .brand-tagline {
    margin-top: 8px;
    font-size: 18px;
    font-weight: 500;
    color: var(--ink-dark);
    line-height: 1.2;
  }
  .divider {
    position: absolute;
    left: 583px;
    top: 205px;
    width: 1px;
    height: 119px;
    background: var(--divider);
  }
  .person {
    position: absolute;
    left: 618px;
    top: 218px;
  }
  .person-name {
    font-size: 36px;
    font-weight: 400;
    color: var(--ink-dark);
    line-height: 1.1;
    letter-spacing: 0.5px;
  }
  .person-title {
    font-size: 23px;
    font-weight: 400;
    color: var(--ink-muted);
    line-height: 1.2;
  }
  .contact {
    position: absolute;
    left: 0;
    right: 0;
    top: 400px;
    text-align: center;
    color: var(--ink-light);
    font-size: 23px;
    font-style: normal;
    line-height: 33px;
    letter-spacing: 0.2px;
  }
</style>
</head>
<body>
  <article class="business-card">
    <div class="brand-square"></div>
    <div class="brand-text">
      <span class="brand-name">The Linen Loft Co</span>
      <span class="brand-tagline">Calm Spaces, Tidy Homes</span>
    </div>
    <div class="divider"></div>
    <div class="person">
      <p class="person-name">Daniel Hartley</p>
      <p class="person-title">President</p>
    </div>
    <address class="contact">
      <p>Ashby Court, 42 Mill Lane, Leeds LS2 7QT</p>
      <p>0113 496 0721, info@gentlelinenlofts.com</p>
      <p>www.gentlelinenlofts.com</p>
    </address>
  </article>
</body>
</html>
```